Looking for someone to design a business card for my plumbing business Quandor Plumbing Solutions I want the background also to be black, must attract clients. If possible I want the front to be the logo and the back to show maybe the details.

Target Market(s)

Clients

Industry/Entity Type

Plumbing maintenance

Contact Information for Business Card

Name: Felix, Contact: 0461 539 207, Email: quandorplumbingsolutions@mailbrook.example, Licence number 728093K

Font styles to use
Other font styles liked:
• as per logo maybe?

Colors

Designer to choose colors to be used in the design.

Requirements
Nice to have
• stating the service I provide, emergency plumbing, plumbing maintenance, drainage maintenance, block sewer and stormwater, camera and locating.

```html
<!DOCTYPE html>
<html lang="en">
<head>
<meta charset="utf-8">
<title>Quandor Plumbing Solutions – Business Card</title>
<link rel="stylesheet" href="https://fonts.googleapis.com/css2?family=Montserrat:wght@400;500;700;800&display=swap">
<style>
  :root {
    --backdrop: #2b2b2b;
    --card-dark: #141414;
    --blue-light: #9cc8ec;
    --blue-mid: #5198d4;
    --blue-deep: #1d5a99;
    --accent: #4a8fd6;
    --white: #ffffff;
  }
  * { margin: 0; padding: 0; box-sizing: border-box; }
  html, body {
    width: 1200px; height: 689px; overflow: hidden;
    background: var(--backdrop);
    font-family: "Montserrat", sans-serif;
  }
  .canvas {
    position: relative; width: 1200px; height: 689px;
    display: flex; align-items: center; justify-content: center; gap: 60px;
  }
  .card {
    position: relative; width: 520px; height: 318px;
    border-radius: 24px; overflow: hidden;
  }
  .card--front {
    background: linear-gradient(115deg, var(--blue-light) 0%, var(--blue-mid) 55%, var(--blue-mid) 100%);
    display: flex; align-items: center; justify-content: center;
  }
  .brand {
    display: flex; align-items: center; gap: 14px;
  }
  .brand__mark {
    width: 26px; height: 26px; border-radius: 50%;
  }
  .brand__name {
    font-weight: 800; text-transform: uppercase; line-height: 1.05;
    letter-spacing: 0.02em;
  }
  .card--front .brand__mark { background: var(--blue-deep); }
  .card--front .brand__name { color: var(--blue-deep); font-size: 30px; }

  .card--back { background: var(--card-dark); }
  .card--back .brand {
    position: absolute; left: 150px; top: 52px;
  }
  .card--back .brand__mark { background: var(--accent); width: 20px; height: 20px; }
  .card--back .brand__name { color: var(--white); font-size: 22px; }

  .contact {
    position: absolute; left: 44px; top: 176px;
  }
  .contact__name {
    color: var(--accent); font-weight: 800; font-size: 34px; margin-bottom: 16px;
  }
  .contact__line {
    display: flex; align-items: center; gap: 10px;
    color: var(--white); font-size: 13px; font-weight: 500; margin-bottom: 8px;
  }
  .contact__icon { width: 14px; height: 14px; flex: none; }
  .licence {
    position: absolute; right: 28px; top: 120px;
    color: var(--white); font-size: 13px; font-weight: 400;
  }
</style>
</head>
<body>
<main class="canvas">
  <section class="card card--front" aria-label="Card front">
    <div class="brand">
      <span class="brand__mark"></span>
      <span class="brand__name">Quandor<br>Plumbing Solutions</span>
    </div>
  </section>

  <section class="card card--back" aria-label="Card back">
    <div class="brand">
      <span class="brand__mark"></span>
      <span class="brand__name">Quandor<br>Plumbing Solutions</span>
    </div>

    <p class="licence">Licence number 728093K</p>

    <div class="contact">
      <p class="contact__name">Felix</p>
      <p class="contact__line">
        <svg class="contact__icon" viewBox="0 0 24 24" aria-hidden="true">
          <path fill="#4a8fd6" d="M6.6 10.8a15 15 0 0 0 6.6 6.6l2.2-2.2c.3-.3.7-.4 1-.2 1.1.4 2.3.6 3.6.6.6 0 1 .4 1 1V20c0 .6-.4 1-1 1A17 17 0 0 1 3 4c0-.6.4-1 1-1h3.5c.6 0 1 .4 1 1 0 1.3.2 2.5.6 3.6.1.3 0 .7-.2 1z"/>
        </svg>
        0461 539 207
      </p>
      <p class="contact__line">
        <svg class="contact__icon" viewBox="0 0 24 24" aria-hidden="true">
          <rect x="2" y="5" width="20" height="14" rx="1.5" fill="#4a8fd6"/>
          <path d="M3 6l9 7 9-7" fill="none" stroke="#141414" stroke-width="1.6"/>
        </svg>
        quandorplumbingsolutions@mailbrook.example
      </p>
    </div>
  </section>
</main>
</body>
</html>
```